Young Architect Bussiness Card

English is not my first language (spanish is).
Need a bussiness card design for my best friend who is about to graduate from college, Licentiate degree in architecture, so she needs business cards to start networking, currently she has no porfolio, web page or plazared. so she is relying on her cel phone and correovela, but should leave space for one of them (plazared)

Design for business card should be modern, maybe something with construction blue prints patern or 3D modelling.

Name: Mariela Otárola Bonilla
Licentiate in Arquitecture
Cel: (506) XXX-4827
email: marielaXXX@correovela.com

Services, although im not sure if it has to be there or not:
Anteproyectos / Proposal design
Inspecciones / Site Inspections
Modelado 3D / 3D modelling
Planos Constructivos / Construction Blue Prints
Presupuestos / Budgets

Design should be in spanish

Industry/Entity Type

Architect

Contact Information for Business Card

Name: Mariela Otárola, Arquitecto
Associtation code : XXXX
Phone: (506) XXXX-XXXX
Email: xxx@correovela.com
Plazared: xxxx

Requirements
Must have
• Design for business card should be modern, maybe something with construction blue prints patern or 3D modelling.
Nice to have
• Something like a transition from 2D to 3D.

```html
<!DOCTYPE html>
<html lang="es">
<head>
<meta charset="utf-8">
<title>Tarjeta de presentación – Mariela Otárola Bonilla</title>
<link rel="stylesheet" href="https://fonts.googleapis.com/css2?family=Tinos:wght@400;700&family=Open+Sans:wght@400;600&display=swap">
<style>
  :root {
    --page: #e8e2d8;
    --cream: #f1efe8;
    --paper: #eeeeec;
    --blue: #1a6aa8;
    --text-blue: #1f6cb0;
    --red: #a3122e;
    --ink: #141414;
    --white: #f6f6f2;
    --photo-yellow: #f2c230;
    --photo-sky: #cfdde6;
  }
  * { margin: 0; padding: 0; box-sizing: border-box; }
  html, body { width: 1200px; height: 823px; overflow: hidden; background: var(--page); }
  .canvas { position: relative; width: 1200px; height: 823px; }

  .card {
    position: absolute; top: 256px; width: 540px; height: 310px;
    overflow: hidden; box-shadow: 0 6px 18px rgba(0,0,0,.18);
  }
  .card--services { left: 40px; background: var(--paper); }
  .card--front { left: 620px; background: var(--cream); }

  /* Services side */
  .blueprint-bg {
    position: absolute; inset: 0;
    background: linear-gradient(135deg, #f4f4f2 0%, #e4e5e3 55%, #ececea 100%);
  }
  .services { position: absolute; left: 92px; top: 70px; font-family: "Open Sans", sans-serif; }
  .services__title {
    position: absolute; left: 200px; top: -38px;
    color: var(--red); font-size: 24px; font-weight: 600; letter-spacing: .5px;
  }
  .services__dots { position: absolute; left: -62px; top: 6px; display: flex; gap: 8px; }
  .services__dots span { width: 9px; height: 9px; border-radius: 50%; background: var(--red); }
  .services__list { list-style: none; color: var(--text-blue); font-size: 16px; line-height: 22px; }

  /* Front side */
  .front-shapes { position: absolute; inset: 0; }
  .identity { position: absolute; right: 22px; top: 70px; text-align: right; font-family: "Tinos", serif; color: var(--ink); }
  .identity__name { font-size: 27px; font-weight: 700; }
  .identity__title { font-size: 15px; font-weight: 700; margin-top: 2px; }
  .contact {
    position: absolute; right: 22px; top: 166px; text-align: right;
    font-family: "Tinos", serif; color: var(--white); font-size: 15px; line-height: 20px;
  }
  .contact__row { display: flex; justify-content: flex-end; align-items: center; gap: 6px; }
  .contact__gap { height: 14px; }
  .contact__mark { width: 10px; height: 10px; border: 1.5px solid var(--white); border-radius: 2px; }
  .contact svg { width: 12px; height: 10px; }
</style>
</head>
<body>
<div class="canvas">

  <section class="card card--services">
    <div class="blueprint-bg" role="img" aria-label="Faint architectural blueprint drawing of a house in light grey lines"></div>
    <div class="services">
      <div class="services__title">Services</div>
      <div class="services__dots"><span></span><span></span><span></span><span></span></div>
      <ul class="services__list">
        <li>Anteproyectos / Proposal design</li>
        <li>Inspecciones / Site Inspections</li>
        <li>Modelado 3D / 3D modelling</li>
        <li>Planos Constructivos / Construction Blue Prints</li>
        <li>Presupuestos / Budgets</li>
      </ul>
    </div>
  </section>

  <section class="card card--front">
    <svg class="front-shapes" width="540" height="310" viewBox="0 0 540 310">
      <defs>
        <linearGradient id="photoTone" x1="0" y1="0" x2="1" y2="1">
          <stop offset="0" stop-color="var(--photo-yellow)"/>
          <stop offset=".45" stop-color="#f5d46a"/>
          <stop offset="1" stop-color="var(--photo-sky)"/>
        </linearGradient>
      </defs>
      <polygon class="front-photo" points="0,0 205,0 265,145 228,310 0,310" fill="url(#photoTone)" role="img" aria-label="Photo of a yellow hard hat, rolled blueprints, folding ruler and spirit level on construction plans"/>
      <polyline points="205,0 265,145" stroke="var(--blue)" stroke-width="5" fill="none"/>
      <polyline points="265,145 228,310" stroke="var(--cream)" stroke-width="6" fill="none"/>
      <polygon class="contact-band" points="276,140 540,140 540,310 240,310" fill="var(--blue)"/>
    </svg>

    <div class="identity">
      <div class="identity__name">Mariela Otárola Bonilla</div>
      <div class="identity__title">Licentiate in Arquitecture</div>
    </div>

    <div class="contact">
      <div class="contact__row">Associtation code : XXXX</div>
      <div class="contact__row">Plazared: xxxx <span class="contact__mark"></span></div>
      <div class="contact__gap"></div>
      <div class="contact__row">(506) XXX-4827
        <svg viewBox="0 0 12 10"><rect x=".75" y=".75" width="10.5" height="8.5" rx="1" fill="none" stroke="var(--white)" stroke-width="1.3"/><polyline points="1,1.5 6,5.5 11,1.5" fill="none" stroke="var(--white)" stroke-width="1.3"/></svg>
      </div>
      <div class="contact__row">marielaXXX@correovela.com</div>
      <div class="contact__row">www.trazonorte.com</div>
    </div>
  </section>

</div>
</body>
</html>
```